Business Card Design For A Cajun Seafood Restaurant

We are opening a cajun seafood restaurant in a week. We mainly serve cajun seafood which is orginally from Louisiana. We want design on both sides of a business card. I have menu on the website. You can go to www.reednkettle.example to check out our menu.

Restaurant name: Reed N' Kettle
Phone: +1 (555) 304-7712
Address: 48206 Ludlow Row, #7, Bexmoor Flats, Ca90000
Email: reednkettle@mailbox.example
Website: www.reednkettle.example

Maybe add social media icons (facebook, instagram) if looks nice on the business card.
facebook.com/reednkettle
instagram.com/reednkettle or @reednkettle

Attached is the logo and other business card samples that I like.

```html
<!DOCTYPE html>
<html lang="en">
<head>
<meta charset="utf-8">
<title>Reed N' Kettle — Business Card</title>
<link rel="stylesheet" href="https://fonts.googleapis.com/css2?family=Open+Sans:wght@400;700;800&display=swap">
<style>
  :root {
    --page: #ecebe8;
    --ink: #222222;
    --card-dark: #050505;
    --card-light: #ffffff;
    --brand-orange: #f26a10;
    --brand-yellow: #fcc417;
  }
  * { box-sizing: border-box; margin: 0; padding: 0; }
  html, body { width: 1200px; height: 900px; overflow: hidden; }
  body {
    background: var(--page);
    font-family: "Open Sans", Arial, sans-serif;
    color: var(--ink);
    position: relative;
  }
  .card {
    position: absolute;
    left: 270px;
    width: 660px;
    height: 377px;
    border-radius: 4px;
    overflow: hidden;
    box-shadow: 0 6px 18px rgba(0,0,0,.18);
  }
  .card--front { top: 48px; background: var(--card-dark); }
  .card--back { top: 475px; background: var(--card-light); }

  .brand {
    position: absolute;
    font-weight: 800;
    white-space: nowrap;
    line-height: 1;
  }
  .card--front .brand {
    left: 50%; top: 50%;
    transform: translate(-50%, -50%);
    font-size: 42px;
    color: var(--brand-yellow);
  }
  .card--back .brand {
    right: 48px; top: 140px;
    font-size: 30px;
    color: var(--ink);
  }

  .social { position: absolute; left: 44px; top: 34px; font-size: 14px; line-height: 20px; }
  .social li, .contact li { list-style: none; display: flex; align-items: center; gap: 8px; }
  .social__mark { width: 11px; height: 11px; border-radius: 2px; background: var(--brand-orange); }

  .address { position: absolute; left: 44px; top: 92px; font-size: 15px; line-height: 20px; font-style: normal; }

  .contact { position: absolute; left: 44px; top: 180px; font-size: 15px; line-height: 22px; }
  .contact svg { width: 12px; height: 12px; fill: var(--brand-orange); }

  .bands { position: absolute; left: 0; bottom: 0; width: 660px; height: 64px; }
  .bands .band-yellow { fill: var(--brand-yellow); }
  .bands .band-orange { fill: var(--brand-orange); }
</style>
</head>
<body>

<section class="card card--front" aria-label="Card front">
  <div class="brand">Reed N' Kettle</div>
</section>

<section class="card card--back" aria-label="Card back">
  <ul class="social">
    <li><span class="social__mark"></span>reednkettle</li>
    <li><span class="social__mark"></span>reednkettle</li>
  </ul>

  <address class="address">
    48206 Ludlow Row, #7,<br>Bexmoor Flats, Ca90000
  </address>

  <ul class="contact">
    <li>
      <svg viewBox="0 0 24 24" aria-hidden="true"><path d="M6.6 10.8a15 15 0 0 0 6.6 6.6l2.2-2.2a1 1 0 0 1 1-.25 11.4 11.4 0 0 0 3.6.57 1 1 0 0 1 1 1V20a1 1 0 0 1-1 1A17 17 0 0 1 3 4a1 1 0 0 1 1-1h3.5a1 1 0 0 1 1 1c0 1.25.2 2.45.57 3.6a1 1 0 0 1-.25 1z"/></svg>
      +1 (555) 304-7712
    </li>
    <li>
      <svg viewBox="0 0 24 24" aria-hidden="true"><path d="M2 5h20v14H2z"/></svg>
      reednkettle@mailbox.example
    </li>
    <li>
      <svg viewBox="0 0 24 24" aria-hidden="true"><circle cx="12" cy="12" r="10"/></svg>
      www.reednkettle.example
    </li>
  </ul>

  <div class="brand">Reed N' Kettle</div>

  <svg class="bands" viewBox="0 0 660 64" preserveAspectRatio="none" aria-hidden="true">
    <polygon class="band-yellow" points="0,0 292,0 280,26 0,26"/>
    <polygon class="band-orange" points="300,0 660,0 660,64 272,64"/>
  </svg>
</section>

</body>
</html>
```